Tolvik Commercial Cleaning is lookong for a new business card design.

A fresh new design that's professional and stylish. We need a serious upgrade to our business cards. I have included pictures of our existing ones. Our clients include professional individuals and business owners. We woupdblike something professional and upbeat. Please have fun and see what you come uo with.

Target Market(s)

Property managers, business owners, facility managers and other similar professionals

Industry/Entity Type

Janitorial

Contact Information for Business Card

Name, cell, office number, email, web address

Font styles to use
Sans Serif

Colors

Designer to choose colors to be used in the design.

Requirements
Must have
• please use the green color in our logo
Nice to have
• Bar code
Should not have
• Address

```html
<!DOCTYPE html>
<html lang="en">
<head>
<meta charset="utf-8">
<title>Tolvik Commercial Cleaning – Business Card</title>
<link rel="stylesheet" href="https://fonts.googleapis.com/css2?family=Open+Sans:wght@400;700&display=swap">
<style>
  :root {
    --stage: #333333;
    --brand-green: #3bb75a;
    --deep-green: #2f8f47;
    --card-dark: #1f1f22;
    --accent-blue: #3a6fb5;
    --ink-light: #ffffff;
    --ghost-mark: #2a2a2e;
  }
  * { box-sizing: border-box; margin: 0; padding: 0; }
  html, body {
    width: 1200px; height: 780px; overflow: hidden;
    background: var(--stage);
    font-family: "Open Sans", Arial, sans-serif;
  }
  .canvas {
    width: 1200px; height: 780px;
    display: flex; align-items: center; justify-content: center; gap: 40px;
  }
  .card {
    position: relative; width: 540px; height: 309px; overflow: hidden;
    border-radius: 2px;
  }
  /* Front */
  .card--front {
    background: var(--brand-green);
    display: flex; align-items: center; justify-content: center;
  }
  .front-name {
    color: var(--deep-green); font-weight: 700; text-align: center;
    line-height: 1.05;
  }
  .front-name__main { display: block; font-size: 74px; letter-spacing: -1px; }
  .front-name__sub { display: block; font-size: 22px; letter-spacing: 1px; margin-top: 6px; }

  /* Back */
  .card--back { background: var(--card-dark); }
  .ghost-name {
    position: absolute; right: -34px; top: 50%;
    transform: translateY(-50%) rotate(90deg);
    color: var(--ghost-mark); font-weight: 700; font-size: 96px;
    letter-spacing: -2px; white-space: nowrap;
  }
  .brand {
    position: absolute; left: 40px; top: 38px;
    color: var(--brand-green); font-weight: 700; line-height: 1.05;
  }
  .brand__main { display: block; font-size: 50px; letter-spacing: -1px; }
  .brand__sub { display: block; font-size: 15px; letter-spacing: .5px; margin-top: 2px; }
  .person {
    position: absolute; left: 40px; top: 172px;
    font-weight: 700; font-size: 30px; letter-spacing: .3px;
  }
  .person__first { color: var(--brand-green); }
  .person__last { color: var(--accent-blue); }
  .contacts {
    position: absolute; left: 40px; top: 220px; list-style: none;
    color: var(--ink-light); font-size: 15px; line-height: 23px;
  }
  .contacts li { display: flex; align-items: center; gap: 10px; }
  .contacts svg { width: 14px; height: 14px; flex: none; fill: var(--brand-green); }
</style>
</head>
<body>
<main class="canvas">
  <section class="card card--front" aria-label="Card front">
    <p class="front-name">
      <span class="front-name__main">Tolvik</span>
      <span class="front-name__sub">Commercial Cleaning</span>
    </p>
  </section>

  <section class="card card--back" aria-label="Card back">
    <span class="ghost-name" aria-hidden="true">Tolvik</span>
    <p class="brand">
      <span class="brand__main">Tolvik</span>
      <span class="brand__sub">Commercial Cleaning</span>
    </p>
    <h1 class="person"><span class="person__first">Marco</span> <span class="person__last">Delgado</span></h1>
    <ul class="contacts">
      <li>
        <svg viewBox="0 0 24 24" aria-hidden="true"><path d="M6.6 10.8a15.1 15.1 0 0 0 6.6 6.6l2.2-2.2a1 1 0 0 1 1-.25 11.4 11.4 0 0 0 3.6.57 1 1 0 0 1 1 1V20a1 1 0 0 1-1 1A17 17 0 0 1 3 4a1 1 0 0 1 1-1h3.5a1 1 0 0 1 1 1c0 1.25.2 2.45.57 3.6a1 1 0 0 1-.25 1z"/></svg>
        (555) 014-2873
      </li>
      <li>
        <svg viewBox="0 0 24 24" aria-hidden="true"><path d="M2 5h20v14H2z M4 7v.5l8 5 8-5V7z" fill-rule="evenodd"/></svg>
        marco@tolvikcleaning.com
      </li>
      <li>
        <svg viewBox="0 0 24 24" aria-hidden="true"><path d="M12 2a10 10 0 1 0 0 20 10 10 0 0 0 0-20zm6.9 6h-3a15 15 0 0 0-1.3-3.9A8 8 0 0 1 18.9 8zM12 4c.8 1.2 1.5 2.5 1.9 4h-3.8c.4-1.5 1.1-2.8 1.9-4zM4.3 14a8 8 0 0 1 0-4h3.3a16 16 0 0 0 0 4zm.8 2h3a15 15 0 0 0 1.3 3.9A8 8 0 0 1 5.1 16zm3-8h-3a8 8 0 0 1 4.3-3.9A15 15 0 0 0 8.1 8zM12 20c-.8-1.2-1.5-2.5-1.9-4h3.8c-.4 1.5-1.1 2.8-1.9 4zm2.3-6H9.7a14 14 0 0 1 0-4h4.6a14 14 0 0 1 0 4zm.3 5.9a15 15 0 0 0 1.3-3.9h3a8 8 0 0 1-4.3 3.9zm1.8-5.9a16 16 0 0 0 0-4h3.3a8 8 0 0 1 0 4z"/></svg>
        www.tolvikcleaning.com
      </li>
    </ul>
  </section>
</main>
</body>
</html>
```